Create website for home automation - Control your lighting, fans, blinds etc remotely by smartphone

Plan for SHOPIFY Website - Our Clever Dwelling
Company name: Our Clever Dwelling
Company Slogan: Calm Evenings Come Naturally
Clean, Modern, Easy to Navigate, easy to maintain - not a lot of coding. We need flash technology but displaying simply what we do.
What we provide:
We will be offering wireless switch which can be added to iOS/Android App via WiFi, allowing users to remotely turn on/off connected lights, fans, security cameras, appliances, irrigation, humidifier separately from anywhere at any time.
Control your home away from home. No more wandering of your mind on those lights or appliances which you might have left switched on. No need to drive back home to check and switch them off. Save that energy, money and time just with a click of your phone no matter how far you are from home.
Replace your home electrical switches with smart switches. They retrofit existing electrical switches and allow you to make the transformation as needed.
Easy to use and intuitive app allows you to control your lights and devices just at a click. Set any kind of ambiance suiting your occasion.
Set scenes in smartphone app to group and operate your devices just at a button click. Same device can be included in more than one scene.
Collections and Products
Light Switches
Wall Plugs
Fan Switch
Pendants etc special lighting types.
Light Dimmers
Blind Controllers
Home Page:
Home page needs to telling customers what we do and how we do it in a few words to grab people.
Phone
Email
Support – Download instructions per product
Client login
Wholesale login
Promotional video to be on home screen - this is a short 1.5 - 2 min illustration introduction video to who we are and what we do - this is yet to be created)
Social media link - Facebook
Pages:
FAQ
About Us
Support/Shipping/Returns policy
Support/Installation
Blog posts
Product pages:
Description
Price
Space for where a video will be featured - how each product works/installation.
Reviews
Our competition:
http://www.brivo.com.au
https://lumigardenhub.com.au/2018/04/05/best-smart-light-switches-and-plugs/
https://www.tavelinq.com

```html
<!DOCTYPE html>
<html lang="en">
<head>
<meta charset="utf-8">
<title>Contact Us – Our Clever Dwelling</title>
<link href="https://fonts.googleapis.com/css2?family=Didact+Gothic&family=Open+Sans:wght@400;600;700&display=swap" rel="stylesheet">
<style>
:root{
  --brand:#1a5fb4;
  --navy:#15306b;
  --ink:#1b1b1b;
  --muted:#555;
  --line:#bdbdbd;
  --footer:#0e0e0e;
  --white:#ffffff;
}
*{box-sizing:border-box;margin:0;padding:0}
html,body{width:1012px;height:1200px;overflow:hidden;background:var(--white)}
body{position:relative;font-family:"Open Sans",sans-serif;color:var(--ink)}
.site-header{position:absolute;left:0;top:0;width:1012px;height:127px;border-bottom:1px solid var(--line)}
.brand{position:absolute;left:70px;top:44px;display:flex;align-items:center;gap:8px;color:var(--navy);font-family:"Open Sans",sans-serif;font-weight:700;font-size:15px;letter-spacing:.3px}
.brand-mark{width:14px;height:14px;background:var(--navy)}
.main-nav{position:absolute;top:53px;left:322px;display:flex;font-family:"Didact Gothic",sans-serif;font-size:17px}
.main-nav a{color:var(--ink);text-decoration:none;margin-right:26px}
.main-nav a.is-current{color:var(--brand)}
.header-tools{position:absolute;top:55px;left:846px;display:flex;gap:18px;align-items:center}
.cart{position:relative}
.cart-count{position:absolute;top:-6px;left:5px;width:10px;height:10px;border-radius:50%;background:var(--brand);color:#fff;font-size:7px;line-height:10px;text-align:center}
.page-title{position:absolute;top:164px;width:1012px;text-align:center;font-family:"Didact Gothic",sans-serif;font-weight:400;font-size:41px}
.page-intro{position:absolute;top:230px;width:1012px;text-align:center;font-size:17px;color:#2a2a2a}
.divider{position:absolute;left:160px;top:274px;width:697px;height:1px;background:#aaa}
.field-label{position:absolute;font-size:18px;color:#2a2a2a}
.field{position:absolute;width:697px;height:57px;border:1px solid #a9a9a9;padding-left:18px;font-size:14px;line-height:55px;color:#444}
.field.message{height:110px}
.submit{position:absolute;left:164px;top:802px;width:117px;height:43px;background:var(--brand);color:#fff;font-size:20px;text-align:center;line-height:43px}
.footer-band{position:absolute;top:910px;left:0;width:1012px;height:9px;background:var(--brand)}
.site-footer{position:absolute;top:919px;left:0;width:1012px;height:281px;background:var(--footer);color:#fff}
.footer-heading{position:absolute;font-size:14px;letter-spacing:.2px}
.footer-list{position:absolute;list-style:none;font-size:12px;line-height:20px}
.footer-list li::before{content:"» ";}
.contact-block{position:absolute;left:476px;top:92px;font-size:12px;line-height:18.5px;width:250px}
.contact-block p{margin-bottom:4.5px}
.social{position:absolute;left:781px;top:102px;display:flex;gap:13px}
.social span{width:20px;height:20px;border-radius:3px;background:#fff}
.footer-rule{position:absolute;left:73px;top:216px;width:863px;height:1px;background:#2a2a2a}
.copyright{position:absolute;top:237px;width:1012px;text-align:center;font-size:13px;padding-left:20px}
</style>
</head>
<body>
<header class="site-header">
  <div class="brand"><span class="brand-mark"></span>Our Clever Dwelling</div>
  <nav class="main-nav">
    <a href="#">Home</a><a href="#">About Us</a><a href="#">Products</a><a href="#">Support</a><a href="#">Blog</a><a href="#">FAQ</a><a href="#" class="is-current">Contact</a>
  </nav>
  <div class="header-tools">
    <svg width="16" height="16" viewBox="0 0 16 16" aria-label="Search"><circle cx="6.5" cy="6.5" r="5" fill="none" stroke="#111" stroke-width="2.4"/><line x1="10" y1="10" x2="15" y2="15" stroke="#111" stroke-width="2.8" stroke-linecap="round"/></svg>
    <span class="cart"><svg width="18" height="15" viewBox="0 0 18 15" aria-label="Basket"><path d="M1 5h16l-2 9H3z" fill="#111"/><path d="M5 5l3-4M13 5l-3-4" stroke="#111" stroke-width="1.6"/><rect x="6" y="7" width="1.4" height="5" fill="#fff"/><rect x="10.6" y="7" width="1.4" height="5" fill="#fff"/></svg><span class="cart-count">1</span></span>
    <svg width="20" height="18" viewBox="0 0 20 18" aria-label="Account" style="margin-left:4px"><circle cx="10" cy="5" r="4.5" fill="#111"/><path d="M2 18c0-6 4-8 8-8s8 2 8 8z" fill="#111"/></svg>
  </div>
</header>

<main>
  <h1 class="page-title">Contact Us</h1>
  <p class="page-intro">We're always happy to help! Please reach out to us using the contact form below.</p>
  <div class="divider"></div>

  <label class="field-label" style="left:162px;top:312px">Name</label>
  <div class="field" style="left:162px;top:345px">Your name</div>
  <label class="field-label" style="left:162px;top:423px">Email</label>
  <div class="field" style="left:162px;top:456px;padding-left:16px">your@email.com</div>
  <label class="field-label" style="left:164px;top:531px">Phone</label>
  <div class="field" style="left:164px;top:564px"></div>
  <label class="field-label" style="left:164px;top:639px">Message</label>
  <div class="field message" style="left:164px;top:672px"></div>
  <div class="submit">Submit</div>
</main>

<div class="footer-band"></div>
<footer class="site-footer">
  <h2 class="footer-heading" style="left:77px;top:55px;font-weight:400">INFORMATION</h2>
  <ul class="footer-list" style="left:77px;top:88px"><li>Privacy Policy</li><li>Your Account</li><li>Advanced Search</li><li>Contact Us</li></ul>
  <h2 class="footer-heading" style="left:302px;top:56px;font-weight:400">LINKS</h2>
  <ul class="footer-list" style="left:303px;top:90px"><li>Home</li><li>About us</li><li>Products</li><li>Shop</li></ul>
  <h2 class="footer-heading" style="left:473px;top:56px;font-weight:400">CONTACT US</h2>
  <div class="contact-block">
    <p>Address : 48-52 Harrowgate - Elmsworth Road, Elmsworth, Canada</p>
    <p>Phone :&nbsp; (03) 5520 4417,&nbsp; (04) 2268 9351</p>
    <p>Email : hello@ourcleverdwelling.com.au</p>
  </div>
  <h2 class="footer-heading" style="left:780px;top:52px;font-weight:400">FOLLOW US OUT THERE</h2>
  <div class="social"><span></span><span></span><span></span><span></span></div>
  <div class="footer-rule"></div>
  <p class="copyright">Copyright © 2018. All Rights Reserved</p>
</footer>
</body>
</html>
```